i need a business card design for my family investment company "quorin investments" based in dubai. its a diverse investment firm focusing on education, hospitality and automotive. the design has to be modern and try to incorporate the logo "E" in the design. details on card as follow

Yusuf K Bin Tarrah
Managing Director
yusuf@quorin-mail.ae
www.quorin-mail.ae

Harbor district,palwick tower, office 2212, dubai
tel. 04 3850927
mobile.050 9184203

card used for networking events and investor meetings

Hospitality

```html
<!DOCTYPE html>
<html lang="en">
<head>
<meta charset="utf-8">
<title>Quorin Investments – Business Card</title>
<link rel="stylesheet" href="https://fonts.googleapis.com/css2?family=Lato:wght@300;400;700&display=swap">
<style>
  :root {
    --page-bg: #e9e7e3;
    --card-white: #fbfbfb;
    --ink: #3a3d42;
    --ink-soft: #5b6068;
    --brand-blue: #4f86ad;
    --brand-blue-deep: #3a6b93;
    --back-light: #7fb4cf;
    --back-mid: #5a93b8;
    --back-dark: #3e6d92;
    --back-ink: #f4f8fb;
  }
  * { box-sizing: border-box; margin: 0; padding: 0; }
  html, body { width: 1200px; height: 1023px; overflow: hidden; }
  body {
    background: var(--page-bg);
    font-family: "Lato", Arial, sans-serif;
    position: relative;
  }
  .card {
    position: absolute;
    width: 600px;
    height: 343px;
    border-radius: 26px;
    overflow: hidden;
    box-shadow: 0 10px 28px rgba(0,0,0,.18);
  }

  /* Front */
  .card--front { left: 70px; top: 80px; background: var(--card-white); }
  .front-brand {
    position: absolute; right: 48px; top: 52px;
    color: var(--ink); font-weight: 300; text-align: right;
    letter-spacing: 10px; font-size: 34px; line-height: 1;
  }
  .front-brand small {
    display: block; font-size: 11px; letter-spacing: 9px; margin-top: 8px;
  }
  .name-tab {
    position: absolute; left: 0; top: 150px;
    width: 250px; height: 62px;
    background: linear-gradient(180deg, var(--brand-blue), var(--brand-blue-deep));
    border-radius: 0 31px 31px 0;
    padding: 11px 0 0 30px; color: #fff;
  }
  .name-tab__name { font-weight: 700; font-size: 18px; }
  .name-tab__title { font-weight: 400; font-size: 13px; opacity: .9; margin-top: 2px; }
  .company {
    position: absolute; left: 30px; top: 230px;
    color: var(--ink); font-size: 13px; line-height: 1.4;
  }
  .company__name { color: var(--brand-blue); font-weight: 700; }
  .contacts {
    position: absolute; left: 300px; top: 228px;
    list-style: none; color: var(--ink-soft); font-size: 13px;
  }
  .contacts li { display: flex; align-items: center; gap: 9px; height: 21px; }
  .contacts svg { width: 13px; height: 13px; fill: none; stroke: var(--brand-blue); stroke-width: 1.6; }

  /* Back */
  .card--back {
    left: 530px; top: 590px;
    background: radial-gradient(ellipse at 62% 40%, var(--back-light) 0%, var(--back-mid) 50%, var(--back-dark) 100%);
  }
  .back-brand {
    position: absolute; inset: 0;
    display: flex; flex-direction: column; align-items: center; justify-content: center;
    color: var(--back-ink); font-weight: 300;
  }
  .back-brand__name { font-size: 54px; letter-spacing: 18px; margin-right: -18px; line-height: 1; }
  .back-brand__sub { font-size: 14px; letter-spacing: 12px; margin-right: -12px; margin-top: 14px; }
</style>
</head>
<body>
  <section class="card card--front" aria-label="Card front">
    <div class="front-brand">QUORIN<small>INVESTMENTS</small></div>

    <div class="name-tab">
      <div class="name-tab__name">Yusuf K Bin Tarrah</div>
      <div class="name-tab__title">Managing Director</div>
    </div>

    <div class="company">
      <div class="company__name">Quorin Investments</div>
      <div>Harbor district, palwick tower</div>
      <div>office 2212, dubai</div>
    </div>

    <ul class="contacts">
      <li><svg viewBox="0 0 14 14"><path d="M3 1.5h2.5l1 3-1.6 1a7 7 0 0 0 3.6 3.6l1-1.6 3 1V11a1.5 1.5 0 0 1-1.5 1.5A10 10 0 0 1 1.5 3 1.5 1.5 0 0 1 3 1.5z"/></svg>tel. 04 3850927</li>
      <li><svg viewBox="0 0 14 14"><rect x="3.5" y="1" width="7" height="12" rx="1.2"/><line x1="6" y1="11" x2="8" y2="11"/></svg>mobile. 050 9184203</li>
      <li><svg viewBox="0 0 14 14"><rect x="1" y="3" width="12" height="8" rx="1"/><path d="M1 3l6 5 6-5"/></svg>yusuf@quorin-mail.ae</li>
      <li><svg viewBox="0 0 14 14"><circle cx="7" cy="7" r="5.8"/><path d="M1.2 7h11.6M7 1.2c2.5 3 2.5 8.6 0 11.6M7 1.2c-2.5 3-2.5 8.6 0 11.6"/></svg>www.quorin-mail.ae</li>
    </ul>
  </section>

  <section class="card card--back" aria-label="Card back">
    <div class="back-brand">
      <span class="back-brand__name">QUORIN</span>
      <span class="back-brand__sub">INVESTMENTS</span>
    </div>
  </section>
</body>
</html>
```